Travel Agency Website - Simple General

Need a 7 page simple design that is pretty repetitive. Need to be able to load quickly that is SEO optimized. Trying to give ideas on what they can do, be personal as we are local, but at the same time come across as professional and get information easily with little burden.

- Landing Page
- Brimwell Vacations Page
- Family Trips
- Road Trips from Texas
- Other Destinations
- About Us Page
- Contact Us Page

Target Market(s)

Families

Coding

Coded - Design and coding required

Number of Pages Required

5+ page

Colors

Designer to choose colors to be used in the design.

Requirements
Must have
• Like it to flow easily with our logo. Use that for colors, etc.

```html
<!DOCTYPE html>
<html lang="en">
<head>
<meta charset="utf-8">
<title>About Us | Hum While You Roam Travel</title>
<meta name="description" content="Learn about Hum While You Roam Travel, a local family travel agency delivering joyful, stress-free trip planning.">
<link href="https://fonts.googleapis.com/css2?family=Inter:wght@400;500;600;700;800&display=swap" rel="stylesheet">
<style>
:root{
  --teal:#1d5c6b;
  --teal-dark:#163f4c;
  --gold:#bd8d3f;
  --ink:#1e1e1e;
  --mist:#e4f7fc;
  --white:#ffffff;
  --star:#f4b400;
}
*{box-sizing:border-box;margin:0;padding:0}
html,body{width:1200px;height:2809px;overflow:hidden}
body{font-family:"Inter",sans-serif;color:var(--ink);background:var(--white);position:relative}
.abs{position:absolute}
.topbar{left:0;top:0;width:1200px;height:34px;background:var(--teal);color:var(--white);font-size:16px;display:flex;align-items:center;justify-content:flex-end;padding-right:82px;gap:10px}
.topbar svg{width:16px;height:16px}
.hero{left:0;top:34px;width:1200px;height:453px;background:linear-gradient(180deg,#1b2c38 0%,#2c4a57 45%,#5b6a6c 70%,#7a7466 100%)}
.hero-photo{position:absolute;inset:0;background:radial-gradient(ellipse at 30% 80%,rgba(120,110,95,.6),transparent 60%),linear-gradient(180deg,rgba(15,30,42,.75),rgba(20,35,45,.55))}
.nav{left:67px;top:51px;width:1066px;height:97px;background:var(--white);border-radius:49px;display:flex;align-items:center;padding:0 46px 0 38px}
.brand{display:flex;align-items:center;gap:8px;color:var(--teal);font-weight:700;font-size:15px;line-height:1.1;width:120px}
.brand-dot{width:16px;height:16px;border-radius:50%;background:var(--gold);flex:none}
.nav-links{display:flex;gap:32px;margin-left:auto;margin-right:54px;font-size:17px;color:var(--teal);list-style:none}
.btn{background:var(--gold);color:var(--white);font-weight:600;font-size:15px;padding:11px 17px;border-radius:2px}
.hero-title{left:0;top:246px;width:1200px;text-align:center;color:var(--white);font-size:49px;font-weight:700}
.hero-sub{left:0;top:318px;width:1200px;text-align:center;color:var(--white);font-size:17px;line-height:20px}
.h2{font-size:47px;font-weight:800;color:var(--teal);line-height:57px}
.gold{color:var(--gold)}
.name-heading{left:125px;top:692px;width:400px}
.story{left:125px;top:875px;width:480px;font-size:17px;line-height:20px}
.story p+p{margin-top:20px}
.photo-a{left:663px;top:693px;width:377px;height:254px;border-radius:28px;background:linear-gradient(135deg,#3a2a18 0%,#9b5a20 45%,#e39a3b 60%,#2d2116 100%)}
.photo-b{left:631px;top:987px;width:436px;height:153px;border-radius:18px;border:2px solid var(--teal);background:linear-gradient(90deg,#8a6a58 0%,#c58a5a 50%,#f0a640 100%)}
.frame{left:640px;top:660px}
.center{left:0;width:1200px;text-align:center}
.lede{font-size:17px}
.card{background:var(--white);border-radius:14px;box-shadow:0 2px 8px rgba(0,0,0,.15)}
.feature{top:1449px;width:306px;height:257px;text-align:center;padding:24px 18px}
.feature-icon{width:92px;height:92px;margin:0 auto;border-radius:10px;background:linear-gradient(135deg,#d2a766,#bd8d3f)}
.feature h3{color:var(--teal);font-size:21px;font-weight:600;margin-top:24px}
.feature p{font-size:15px;line-height:18px;margin-top:6px}
.wanderers{left:0;top:1887px;width:1200px;height:638px;background:var(--mist)}
.review{top:2108px;width:306px;height:299px;padding:26px 26px}
.stars{color:var(--star);font-size:24px;letter-spacing:6px;line-height:1}
.review blockquote{font-size:13.5px;line-height:16px;margin-top:20px;height:94px}
.reviewer{display:flex;align-items:center;gap:9px;margin-top:32px}
.avatar{width:52px;height:52px;border-radius:50%;background:var(--gold);color:var(--white);font-weight:600;font-size:20px;display:flex;align-items:center;justify-content:center;flex:none}
.reviewer strong{display:block;color:var(--gold);font-size:20px;font-weight:600}
.reviewer span{font-size:13.5px}
.footer{left:0;top:2525px;width:1200px;height:284px;background:var(--teal);color:var(--white)}
.footer-brand{left:128px;top:2588px;width:167px;height:145px;display:flex;align-items:center;justify-content:center;gap:8px;font-size:20px;font-weight:700;color:var(--white);text-align:left;line-height:1.15}
.fcol{top:2600px}
.fcol h4{color:var(--gold);font-size:20px;font-weight:600;margin-bottom:8px}
.fcol ul{list-style:none;font-size:13.5px}
.fcol li{height:29.5px;display:flex;align-items:center;gap:7px}
.fcol li.bullet::before{content:"";width:5px;height:5px;border-radius:50%;background:var(--gold)}
.fcol svg{width:17px;height:17px}
.social{display:flex;gap:16px;margin-top:8px}
.social span{width:36px;height:36px;border-radius:50%;background:var(--white)}
.divider{left:84px;top:2762px;width:1032px;height:1px;background:rgba(255,255,255,.25)}
.copy{top:2779px;font-size:13.5px;color:var(--white)}
</style>
</head>
<body>
<div class="abs topbar">For More Information Contact Us
  <svg viewBox="0 0 24 24" fill="#bd8d3f"><path d="M6.6 10.8c1.4 2.8 3.8 5.1 6.6 6.6l2.2-2.2c.3-.3.7-.4 1-.2 1.1.4 2.3.6 3.6.6.6 0 1 .4 1 1V20c0 .6-.4 1-1 1C10.6 21 3 13.4 3 4c0-.6.4-1 1-1h3.5c.6 0 1 .4 1 1 0 1.3.2 2.5.6 3.6.1.3 0 .7-.2 1z"/></svg>
  555.010.0199</div>

<header class="abs hero" role="img" aria-label="Family relaxing in beach chairs on a sandy shore with arms raised toward the ocean">
  <div class="hero-photo"></div>
</header>
<nav class="abs nav">
  <div class="brand"><span class="brand-dot"></span>Hum While You Roam</div>
  <ul class="nav-links"><li>Home</li><li>Destinations</li><li>About Us</li><li>Contact Us</li></ul>
  <a class="btn">Plan Your Trip</a>
</nav>
<h1 class="abs hero-title">Our Philosophy: We Hum, You Roam</h1>
<p class="abs hero-sub">Learn about our origins, why we are absolutely obsessed with joyful travel planning,<br>and how we deliver luxury and peace of mind.</p>

<h2 class="abs h2 name-heading">Why the Name "<span class="gold">Hum While You Roam</span>"?</h2>
<div class="abs story">
  <p>Think of the classic, cheerful tune—it's all about finding lighthearted joy, peace, and music in everything you do. Travel planning should never feel like a tedious chore, yet modern bookings have become incredibly complicated with park reservations, genie strategies, rental coordination, and hotel availability puzzles.</p>
  <p>That is where we step in. We hum while we work (doing all the phone calls, holds, complex bookings, and route drafting), so that you can simply hum while you roam. We bring the lightheartedness back to travel, backed by professional expertise and certified planning credentials.</p>
</div>
<svg class="abs frame" width="430" height="320" viewBox="0 0 430 320"><path d="M42 8 L398 58 Q420 62 418 84 L390 290 Q386 314 364 312 L14 262 Q-6 258 4 230 L30 28 Q32 6 42 8 Z" fill="none" stroke="#bd8d3f" stroke-width="2"/></svg>
<div class="abs photo-a" role="img" aria-label="Camper van parked at sunset with glowing lanterns on a small outdoor table"></div>
<div class="abs photo-b" role="img" aria-label="Camper van driving through warm golden evening light"></div>

<h2 class="abs h2 center" style="top:1321px">Why <span class="gold">Hum</span> With Us?</h2>
<p class="abs center lede" style="top:1386px">We take care of every detail so you can focus on making memories.</p>
<article class="abs card feature" style="left:125px"><div class="feature-icon" role="img" aria-label="Itinerary checklist icon"></div><h3>Personalized Planning</h3><p>Every trip is custom-tailored to your preferences, budget, and dreams. No two itineraries are alike.</p></article>
<article class="abs card feature" style="left:447px"><div class="feature-icon" role="img" aria-label="Handshake with star icon"></div><h3>Trusted Partnerships</h3><p>We work with top vendors like Pinecrest Van Rentals to ensure seamless travel experiences.</p></article>
<article class="abs card feature" style="left:769px"><div class="feature-icon" role="img" aria-label="Photos and camera icon"></div><h3>Magical Moments</h3><p>From Brimwell fireworks to hidden Texas gems, we know how to find the magic in every journey.</p></article>

<section class="abs wanderers"></section>
<h2 class="abs h2 center" style="top:1984px">What Happy <span class="gold">Wanderers</span> Say</h2>
<article class="abs card review" style="left:125px"><div class="stars">★★★★★</div><blockquote>"Booking our Brimwell World and Brimwell Cruise vacation with Hum While You Roam was the best decision ever. We didn't have to stay up at 5:00 AM to make dining reservations—they handled everything! Complete bliss."</blockquote><div class="reviewer"><div class="avatar">MF</div><div><strong>The Miller Family</strong><span>Brimwell Cruise &amp; Land Traveler</span></div></div></article>
<article class="abs card review" style="left:447px"><div class="stars">★★★★★</div><blockquote>"Our road trip with Pinecrest Van Rentals was unbelievable. The luxury transit van with reclining captain chairs kept the kids comfortable and quiet. Hum While You Roam co-curated our Hill Country stops flawlessly!"</blockquote><div class="reviewer"><div class="avatar">JH</div><div><strong>James H.</strong><span>Texas Hill Country Wanderer</span></div></div></article>
<article class="abs card review" style="left:769px"><div class="stars">★★★★★</div><blockquote>"We spent two weeks on a tailor-made European vacation. Every transfer was on time, the boutique hotels in Italy were stunning, and our English-speaking guides were so knowledgeable. They really hum while they work!"</blockquote><div class="reviewer"><div class="avatar">SR</div><div><strong>Sarah &amp; Robert</strong><span>European Custom Itinerary</span></div></div></article>

<footer class="abs footer"></footer>
<div class="abs footer-brand"><span class="brand-dot"></span>Hum While<br>You Roam</div>
<div class="abs fcol" style="left:350px"><h4>Destinations</h4><ul><li class="bullet">Brimwell Vacations</li><li class="bullet">Family Trips</li><li class="bullet">Texas Road Trips</li><li class="bullet">Other Destinations</li></ul></div>
<div class="abs fcol" style="left:553px"><h4>Quick Links</h4><ul><li class="bullet">Home</li><li class="bullet">Destination</li><li class="bullet">About Us</li><li class="bullet">Contact Us</li></ul></div>
<div class="abs fcol" style="left:753px"><h4>Contact &amp; Partners</h4><ul>
  <li><svg viewBox="0 0 24 24" fill="#bd8d3f"><path d="M6.6 10.8c1.4 2.8 3.8 5.1 6.6 6.6l2.2-2.2c.3-.3.7-.4 1-.2 1.1.4 2.3.6 3.6.6.6 0 1 .4 1 1V20c0 .6-.4 1-1 1C10.6 21 3 13.4 3 4c0-.6.4-1 1-1h3.5c.6 0 1 .4 1 1 0 1.3.2 2.5.6 3.6.1.3 0 .7-.2 1z"/></svg>&nbsp;555.010.0199</li>
  <li style="font-size:17px"><svg viewBox="0 0 24 24" fill="#bd8d3f"><path d="M3 5h18v14H3z"/><path d="M3 5l9 7 9-7" fill="none" stroke="#1d5c6b" stroke-width="2"/></svg>&nbsp;HumWhileYouRoam@example.com</li></ul>
  <div class="social"><span></span><span></span></div></div>
<div class="abs divider"></div>
<p class="abs center copy">© 2026 Hum While You Roam Travel. All Rights Reserved. Co-branded &amp; developed in partnership with Pinecrest Van Rentals.</p>
</body>
</html>
```